Banner to be displayed at local Farmers Market Booth.

Graphic Design Brief: Farmers Market Banner Contest

Project Overview:We are seeking talented graphic designers to create a visually appealing banner for our booth at the local farmers market. Our company specializes in healthy, all-natural dog and cat treats, and we want a banner that captures our brand identity while drawing in pet owners who value quality and nutrition for their furry friends.

Banner Specifications:

Size: 24 inches x 60 inches (Horizontal orientation) 24" High X 60 wide

Theme: Vintage/Retro

Style: Warm, inviting, nostalgic with a touch of rustic charm

Colors: Earthy, muted tones such as warm browns, soft greens, and creamy yellows. Pops of red or blue may be used sparingly for accents. OR Black and White with gray scales. Would like to see both

Typography: Retro-style fonts that are readable and align with the vintage aesthetic.

Key Elements to Include: website (www.moltbyfarms.com)

Company Name: Moltby Farms

Tagline: " Simply Honest Bites "
Imagery: Illustrations or stylized graphics of happy dogs and cats, possibly interacting with treats.

Emphasis on Natural Ingredients: Icons or design elements that subtly suggest freshness and quality (e.g., leaves, wheat, bones, or paw prints).

Farmers Market Appeal: A design that blends well with the artisanal, handmade, and farm-fresh atmosphere of the market.

Design Considerations:

The banner should be easily readable from a distance.

A balanced composition that doesn't feel overcrowded.

Should evoke trust and warmth while maintaining a professional look.

Avoid overly modern or sleek elements that don’t align with the vintage aesthetic.

Submission Requirements:

High-resolution digital file in PDF or AI format.

CMYK color mode for printing purposes.

Must include a mockup or preview of how it would look in a real farmers market setting.

We look forward to seeing your creative interpretations of our brand! If you have any questions, feel free to reach out.

Font styles to use
Other font styles liked:
• See attachement

Requirements
Nice to have
• Retro/Vintage,playful BUT NOT whimsical

```html
<!DOCTYPE html>
<html lang="en">
<head>
<meta charset="utf-8">
<title>Moltby Farms – Market Banner</title>
<link rel="stylesheet" href="https://fonts.googleapis.com/css2?family=Anton&family=Bowlby+One&family=Sniglet:wght@800&display=swap">
<style>
  :root {
    --page: #dcdcdc;
    --frame: #ebebeb;
    --frame-stripe: #d8d8d8;
    --panel: #2a2a2a;
    --panel-light: #363636;
    --gold: #d9a21a;
    --gold-deep: #8a5a0a;
    --white: #ffffff;
    --ink: #1b1b1b;
    --pill: #c9c9c9;
    --fur-light: #d9a35a;
    --fur-dark: #8a5a26;
  }
  * { box-sizing: border-box; margin: 0; padding: 0; }
  html, body { width: 964px; height: 1200px; overflow: hidden; }
  body { background: var(--page); position: relative; }

  .banner {
    position: absolute; left: 32px; top: 420px;
    width: 900px; height: 360px; overflow: hidden;
    background: repeating-linear-gradient(90deg, var(--frame) 0 4px, var(--frame-stripe) 4px 5px);
    box-shadow: 0 6px 18px rgba(0,0,0,.25);
  }
  .panel-shape { position: absolute; left: 20px; top: 18px; width: 860px; height: 324px; }

  .brand-name {
    position: absolute; left: 60px; top: 36px; width: 480px; text-align: center;
    font-family: "Sniglet", sans-serif; font-weight: 800; font-size: 30px; line-height: 40px;
    color: var(--white); letter-spacing: 1px;
  }
  .tagline {
    position: absolute; left: 60px; top: 86px; width: 480px; text-align: center;
    color: var(--white); line-height: 1; font-weight: 400;
  }
  .tagline-top {
    display: block; font-family: "Anton", sans-serif; font-size: 74px; line-height: 98px; letter-spacing: 1px;
    text-shadow: 2px 2px 0 var(--gold), 3px 3px 0 var(--gold), 5px 4px 0 var(--gold-deep), 6px 6px 6px rgba(0,0,0,.6);
  }
  .tagline-bottom {
    display: block; font-family: "Bowlby One", sans-serif; font-size: 66px; line-height: 86px;
    text-shadow: 2px 2px 0 var(--gold), 3px 3px 0 var(--gold), 5px 4px 0 var(--gold-deep), 6px 6px 6px rgba(0,0,0,.6);
  }
  .website {
    position: absolute; left: 66px; top: 290px; width: 466px; height: 50px;
    background: var(--pill); border: 3px solid var(--ink); border-radius: 16px;
    box-shadow: 0 0 0 4px var(--white);
    font-family: "Sniglet", sans-serif; font-weight: 800; font-size: 36px;
    color: var(--ink); text-align: center; line-height: 42px;
  }
  .pets-photo {
    position: absolute; left: 572px; top: 70px; width: 306px; height: 286px;
    border-radius: 48% 52% 10% 30% / 40% 45% 10% 20%;
    background: radial-gradient(ellipse at 65% 35%, var(--fur-light) 0%, #c08a45 45%, var(--fur-dark) 100%);
  }
</style>
</head>
<body>
  <section class="banner">
    <svg class="panel-shape" viewBox="0 0 860 324" aria-hidden="true">
      <defs>
        <radialGradient id="panelGlow" cx="45%" cy="50%" r="70%">
          <stop offset="0" stop-color="#363636"/>
          <stop offset="1" stop-color="#2a2a2a"/>
        </radialGradient>
      </defs>
      <path d="M40 0 H820 A40 40 0 0 0 860 40 V284 A40 40 0 0 0 820 324 H40 A40 40 0 0 0 0 284 V40 A40 40 0 0 0 40 0 Z"
            fill="url(#panelGlow)" stroke="#d9a21a" stroke-width="3"/>
    </svg>

    <div class="brand-name">Moltby Farms</div>

    <h1 class="tagline">
      <span class="tagline-top">SIMPLY HONEST</span>
      <span class="tagline-bottom">BITES</span>
    </h1>

    <div class="website">moltbyfarms.com</div>

    <div class="pets-photo" role="img" aria-label="Golden retriever lying with a calico cat curled against it"></div>
  </section>
</body>
</html>
```